BUSINESS CARD DESIGN

NAME- DALE VORSKIN
PHONE NUMER - 555- 714-9082
EMAIL- OFFICE@TRV-GROUNDMAKRZ.COM
BACK OF CARD- SPEACIALIZES IN LAND CLEARING, FORESTRY MUCLHING AND EXCAVATION

Contact Information for Business Card

NAME- DALE VORSKIN PHONE NUMER - 555- 714-9082 EMAIL- OFFICE@TRV-GROUNDMAKRZ.COM BACK OF CARD- SPEACIALIZES IN LAND CLEARING , MUCLHING AND EXCAVATION

```html
<!DOCTYPE html>
<html lang="en">
<head>
<meta charset="utf-8">
<title>Terravale Groundmakrz LLC — Business Card</title>
<link rel="stylesheet" href="https://fonts.googleapis.com/css2?family=Audiowide&family=Poppins:wght@400&display=swap">
<style>
  :root {
    --stage: #8a8a8a;
    --card-front: #ffffff;
    --card-back: #000000;
    --ink: #111111;
    --text-dark: #222222;
    --gold: #f2b01e;
    --gold-line: #c99415;
    --white: #ffffff;
  }
  html, body {
    margin: 0;
    padding: 0;
    width: 1093px;
    height: 1200px;
    overflow: hidden;
    background: var(--stage);
  }
  .canvas {
    position: relative;
    width: 1093px;
    height: 1200px;
  }
  .card {
    position: absolute;
    left: 264px;
    width: 580px;
    height: 358px;
    border-radius: 26px;
    overflow: hidden;
  }
  .card--front { top: 226px; background: var(--card-front); }
  .card--back  { top: 621px; background: var(--card-back); }

  /* Front */
  .name-marker {
    position: absolute;
    left: 0; top: 40px;
    width: 18px; height: 18px;
    background: var(--gold);
  }
  .holder-name {
    position: absolute;
    left: 26px; top: 36px;
    margin: 0;
    font: 400 18px/26px "Audiowide", sans-serif;
    color: var(--ink);
    letter-spacing: 0.5px;
  }
  .brand {
    position: absolute;
    text-align: center;
    font-family: "Audiowide", sans-serif;
    font-weight: 400;
  }
  .brand--front { left: 310px; top: 110px; width: 240px; color: var(--ink); }
  .brand--back  { left: 175px; top: 90px;  width: 230px; color: var(--gold); }
  .brand__mark {
    display: block;
    width: 70px; height: 70px;
    margin: 0 auto 14px;
    border-radius: 50%;
    background: currentColor;
  }
  .brand__name { margin: 0; font-size: 21px; line-height: 24px; letter-spacing: 0.5px; }
  .brand__sub  { margin: 4px 0 0; font-size: 11px; line-height: 14px; letter-spacing: 5px; }
  .brand__phone { margin: 6px 0 0; font-size: 9px; line-height: 12px; letter-spacing: 6px; }

  .contact {
    position: absolute;
    left: 26px; top: 259px;
    margin: 0; padding: 0;
    list-style: none;
    font: 400 18px/21px "Poppins", sans-serif;
    color: var(--text-dark);
  }
  .contact li { display: flex; align-items: center; gap: 8px; }
  .contact svg { width: 15px; height: 15px; flex: none; }

  /* Back */
  .specialties-title {
    position: absolute;
    left: 52px; top: 261px;
    width: 478px;
    display: flex; align-items: center; gap: 8px;
    font: 400 17px/24px "Poppins", sans-serif;
    color: var(--white);
    margin: 0;
  }
  .specialties-title::before,
  .specialties-title::after {
    content: ""; flex: 1; height: 1px; background: var(--gold-line);
  }
  .services {
    position: absolute;
    left: 48px; top: 286px;
    margin: 0; padding: 0;
    list-style: none;
    display: flex; gap: 22px;
    font: 400 16.5px/33px "Poppins", sans-serif;
    color: var(--white);
    white-space: nowrap;
  }
  .services li { display: flex; align-items: center; gap: 6px; }
  .service-icon {
    width: 31px; height: 31px;
    border: 1px solid var(--gold-line);
    border-radius: 50%;
    display: flex; align-items: center; justify-content: center;
  }
  .service-icon span { width: 12px; height: 9px; background: var(--gold); border-radius: 2px; }
</style>
</head>
<body>
<main class="canvas">

  <section class="card card--front" aria-label="Business card front">
    <span class="name-marker"></span>
    <h1 class="holder-name">DALE VORSKIN</h1>

    <div class="brand brand--front">
      <span class="brand__mark"></span>
      <p class="brand__name">TERRAVALE</p>
      <p class="brand__sub">GROUNDMAKRZ LLC</p>
      <p class="brand__phone">555-714-9082</p>
    </div>

    <ul class="contact">
      <li>
        <svg viewBox="0 0 16 16" aria-hidden="true"><path d="M3 1l3 3-2 2c1 2 3 4 5 5l2-2 3 3-2 2C7 14 2 9 1 3z" fill="#111"/></svg>
        555- 714-9082
      </li>
      <li>
        <svg viewBox="0 0 16 16" aria-hidden="true"><rect x="1" y="3" width="14" height="10" fill="#111"/><path d="M1 3l7 6 7-6" stroke="#fff" stroke-width="1.2" fill="none"/></svg>
        office@trv-groundmakrz.com
      </li>
      <li>
        <svg viewBox="0 0 16 16" aria-hidden="true" fill="none" stroke="#111" stroke-width="1.3"><circle cx="8" cy="8" r="6.5"/><ellipse cx="8" cy="8" rx="3" ry="6.5"/><path d="M1.5 8h13M2.5 5h11M2.5 11h11"/></svg>
        www.trv-groundmakrz.com
      </li>
    </ul>
  </section>

  <section class="card card--back" aria-label="Business card back">
    <div class="brand brand--back">
      <span class="brand__mark"></span>
      <p class="brand__name">TERRAVALE</p>
      <p class="brand__sub">GROUNDMAKRZ LLC</p>
      <p class="brand__phone">555-714-9082</p>
    </div>

    <h2 class="specialties-title">Specializes In</h2>
    <ul class="services">
      <li><span class="service-icon"><span></span></span>LAND CLEARING</li>
      <li><span class="service-icon"><span></span></span>MULCHING</li>
      <li><span class="service-icon"><span></span></span>EXCAVATION</li>
    </ul>
  </section>

</main>
</body>
</html>
```